Flyer for Compassion training days

I need a A5-size, single-sided flyer design for my training days. They are weekends in a blend of Compassionate Communication and Buddhist teachings called Gentlewise Dialogue. The logo for Gentlewise that should be included.
The flyer needs room for 1) course title, 2) course dates, location & price, 3) course description, 4) booking info, 5) my picture & short bio, and 6) the gentlewise.co website (yes, it is 'co' and not 'com).
Updates

Target Market(s)

Women 35-65 years, well-educated, spiritually minded. May have interests like yoga and meditation.

Industry/Entity Type

Health And Wellness

Font styles to use
Sans Serif
Other font styles liked:
• Blue Plaque, Josefina are both great

Colors
fbf289
fdf9cf
cfeae6
33b8a4

Requirements
Must have
• The Gentlewise logo; my picture.
• Elegance. Calm and expansive feel.
• The poster provided in the project files shows you the kind of information I need to include.
• Colours -- greens and yellows, but the options on craft plaza are not quite the right shades.
• The logo colour can be changed.
Nice to have
• Classy (but not cliche) image associated with Buddhism; gentle curves similar to those on the business card (see project files).
Should not have
• Dark background. Busy, loud design. Overly 'swirly' design. Images that I have to buy separately.

```html
<!DOCTYPE html>
<html lang="en">
<head>
<meta charset="utf-8">
<title>Gentlewise Dialogue – Core Course Flyer</title>
<link rel="stylesheet" href="https://fonts.googleapis.com/css2?family=Josefin+Sans:wght@400;600;700&display=swap">
<style>
  :root {
    --backdrop: #1fb14c;
    --paper: #fbf8dc;
    --paper-glow: #ffffff;
    --brand-green: #22b24c;
    --banner-green: #8cc63f;
    --ink: #2b2b2b;
    --ink-soft: #3a3a3a;
    --bubble: rgba(207, 234, 230, 0.45);
    --bronze-dark: #5a4328;
    --bronze-light: #b89463;
    --photo-dark: #5b4530;
    --photo-light: #b9a27e;
  }
  * { box-sizing: border-box; margin: 0; padding: 0; }
  html, body { width: 1200px; height: 1200px; overflow: hidden; }
  body {
    background: var(--backdrop);
    font-family: "Josefin Sans", sans-serif;
    color: var(--ink);
    position: relative;
  }
  .flyer {
    position: absolute;
    left: 236px; top: 78px;
    width: 736px; height: 1044px;
    background:
      radial-gradient(circle at 55% 48%, var(--paper-glow) 0%, rgba(255,255,255,0) 55%),
      radial-gradient(circle at 88% 36%, var(--bubble) 0 38px, transparent 39px),
      radial-gradient(circle at 75% 44%, var(--bubble) 0 26px, transparent 27px),
      radial-gradient(circle at 92% 74%, var(--bubble) 0 34px, transparent 35px),
      radial-gradient(circle at 12% 96%, var(--bubble) 0 44px, transparent 45px),
      radial-gradient(circle at 70% 96%, var(--bubble) 0 40px, transparent 41px),
      var(--paper);
    overflow: hidden;
  }
  .brand {
    position: absolute; left: 442px; top: 42px;
    display: flex; align-items: center; gap: 12px;
  }
  .brand-dot { width: 64px; height: 64px; border-radius: 50%; background: var(--brand-green); }
  .brand-name { font-size: 25px; font-weight: 600; color: var(--brand-green); padding-top: 4px; }
  .hero-statue {
    position: absolute; left: 40px; top: 80px; width: 212px; height: 308px;
    background: radial-gradient(ellipse at 50% 45%, var(--bronze-light), var(--bronze-dark) 75%, rgba(90,67,40,0) 100%);
    border-radius: 45% 45% 30% 30%;
  }
  .headline {
    position: absolute; left: 266px; width: 410px; top: 206px;
    text-align: center; white-space: nowrap;
  }
  .headline-equation { font-size: 26px; line-height: 36px; font-weight: 400; }
  .headline-title { font-size: 36px; line-height: 46px; font-weight: 700; margin-top: 2px; }
  .course-tag {
    position: absolute; left: 250px; top: 396px; width: 248px; height: 36px;
  }
  .course-tag span {
    position: absolute; inset: 0; display: flex; align-items: center; justify-content: center;
    color: #fff; font-size: 26px; padding-top: 4px;
  }
  .course-meta {
    position: absolute; left: 144px; width: 460px; top: 440px;
    text-align: center; font-size: 24px; line-height: 30px; font-weight: 600;
  }
  .description {
    position: absolute; left: 43px; width: 640px; top: 522px;
    font-size: 14.5px; line-height: 20px; color: var(--ink-soft);
  }
  .description p { margin-bottom: 6px; }
  .topics { list-style: none; margin: 2px 0 8px; }
  .topics li { position: relative; padding-left: 28px; line-height: 21px; }
  .topics li::before {
    content: ""; position: absolute; left: 6px; top: 4px; width: 11px; height: 11px;
    border-radius: 50%; background: var(--brand-green);
  }
  .booking { position: absolute; left: 0; top: 798px; display: flex; align-items: center; }
  .booking-tag { width: 155px; height: 34px; position: relative; }
  .booking-tag span {
    position: absolute; inset: 0; display: flex; align-items: center; padding-left: 28px; padding-top: 4px;
    color: #fff; font-size: 23px;
  }
  .booking-text { margin-left: 10px; font-size: 20px; font-weight: 600; padding-top: 4px; }
  .facilitator-photo {
    position: absolute; left: 46px; top: 865px; width: 136px; height: 131px;
    border-radius: 8px; border: 2px solid #6b5b45;
    background: radial-gradient(circle at 50% 40%, var(--photo-light), var(--photo-dark));
  }
  .facilitator-bio {
    position: absolute; left: 190px; top: 882px; width: 510px;
    font-size: 14.5px; line-height: 18px; font-weight: 600; color: var(--ink-soft);
  }
  .facilitator-bio p { margin-bottom: 6px; }
</style>
</head>
<body>
  <main class="flyer">
    <div class="brand">
      <div class="brand-dot"></div>
      <div class="brand-name">Gentlewise.co</div>
    </div>

    <div class="hero-statue" role="img" aria-label="Bronze seated Buddha statue in meditation pose"></div>

    <header class="headline">
      <div class="headline-equation">Mindfulness + Kindness +<br>Compassionate Communication =</div>
      <h1 class="headline-title">Gentlewise Dialogue</h1>
    </header>

    <div class="course-tag">
      <svg width="248" height="36" viewBox="0 0 248 36"><polygon points="0,0 248,0 236,18 248,36 0,36 12,18" fill="var(--brand-green)"/></svg>
      <span>CORE COURSE</span>
    </div>

    <div class="course-meta">11-12 Dec; Rowan House, Edinburgh<br>(£125/100)</div>

    <section class="description">
      <p>Gentlewise Dialogue can help you increase awareness &amp; compassion in everyday speech (with yourself &amp; others), better understand your own patterns, and build resilience to challenging situations. Choose from:</p>
      <p>In this 2-day Core Course, we’ll explore:</p>
      <ul class="topics">
        <li>Compassionate Communication;</li>
        <li>Buddhist teachings on Right Speech, loving-kindness, Right Effort, and more;</li>
        <li>mindfulness practices;</li>
        <li>choices available to us in our everyday speech.</li>
      </ul>
      <p>This workshop will be of interest if you’d like to improve personal and/or professional relationships. Open to all, best suited to those with at least 1 year’s experience with Mindfulness, Buddhism, or Compassionate Communication / NVC.</p>
    </section>

    <div class="booking">
      <div class="booking-tag">
        <svg width="155" height="34" viewBox="0 0 155 34"><polygon points="0,0 140,0 155,17 140,34 0,34" fill="var(--banner-green)"/></svg>
        <span>BOOKING</span>
      </div>
      <div class="booking-text">Book online at Ticketnest or write maribeth@gentlewise.co</div>
    </div>

    <div class="facilitator-photo" role="img" aria-label="Portrait photo of the facilitator"></div>
    <section class="facilitator-bio">
      <p>Facilitator: Maribeth Ostrander is an experienced group facilitator, having worked with a range of organisations and presented at a number of festivals &amp; conferences.</p>
      <p>Maribeth offers coaching in Gentlewise Dialogue.</p>
      <p>For more info, please visit website www.gentlewise.co</p>
    </section>
  </main>
</body>
</html>
```